Water ATM Card

Need a design for water ATM cards. Size of card is 3.375 x 2.125 inch
On the Front include the Cedar hollow Logo.
Bottom right corner should have Price $100
On the Back
This card is to be used to access water refills at any Cedar Hollow Water Vending Machines.
Please contact (869) 418 2930 or (869) 534 1276 or email clearflowbox@mailvista.example for any assistance or recharging of card.

```html
<!DOCTYPE html>
<html lang="en">
<head>
<meta charset="UTF-8">
<title>Cedar Hollow Water Card</title>
<link rel="stylesheet" href="https://fonts.googleapis.com/css2?family=Poppins:ital,wght@0,400;0,600;0,700;1,600&display=swap">
<style>
  :root {
    --page-bg: #9a9a9a;
    --card-white: #ffffff;
    --brand-blue: #1374bf;
    --brand-blue-deep: #0f6db8;
    --water-pale: #e4f1fb;
    --water-light: #b9d9f1;
    --water-mid: #6fa9da;
    --water-deep: #2f7fc4;
    --text-on-blue: #ffffff;
    --rule: rgba(255,255,255,0.55);
  }
  * { margin: 0; padding: 0; box-sizing: border-box; }
  html, body {
    width: 1093px; height: 1200px; overflow: hidden;
    background: var(--page-bg);
    font-family: "Poppins", sans-serif;
  }
  .card {
    position: absolute;
    left: 265px;
    width: 578px;
    height: 356px;
    border-radius: 20px;
    overflow: hidden;
  }
  /* Front */
  .card--front { top: 226px; background: var(--card-white); }
  .front__water {
    position: absolute; left: 0; top: 0; width: 578px; height: 215px;
    display: block;
  }
  .brand {
    position: absolute; left: 20px; top: 246px; width: 304px;
    display: flex; align-items: center; justify-content: center; gap: 10px;
  }
  .brand__dot {
    width: 18px; height: 18px; border-radius: 50%;
    background: var(--brand-blue); flex: none;
  }
  .brand__name {
    font-family: "Poppins", sans-serif;
    font-weight: 600; font-size: 30px; line-height: 1;
    color: var(--brand-blue);
  }
  .price-tag {
    position: absolute; right: 0; top: 261px;
    width: 168px; height: 43px;
    background: var(--brand-blue);
    border-radius: 22px 0 0 22px;
    color: var(--text-on-blue);
    font-weight: 600; font-size: 22px;
    display: flex; align-items: center; justify-content: center;
    padding-right: 6px;
  }
  /* Back */
  .card--back {
    top: 621px;
    background: var(--brand-blue-deep);
    color: var(--text-on-blue);
    text-align: center;
  }
  .back__water {
    position: absolute; left: 0; top: 0; width: 578px; height: 120px;
    display: block;
  }
  .back__usage {
    position: absolute; left: 0; right: 0; top: 82px;
    font-weight: 700; font-size: 19.5px; line-height: 29px;
    text-transform: uppercase; letter-spacing: -0.2px;
  }
  .back__contact-label {
    position: absolute; left: 60px; right: 60px; top: 202px;
    display: flex; align-items: center; gap: 10px;
    font-size: 17px; font-weight: 400;
  }
  .back__contact-label::before,
  .back__contact-label::after {
    content: ""; flex: 1; height: 1px; background: var(--rule);
  }
  .back__phones {
    position: absolute; left: 0; right: 0; top: 237px;
    font-weight: 600; font-size: 23px;
  }
  .back__or { font-weight: 400; font-size: 16px; }
  .back__email-line {
    position: absolute; left: 0; right: 0; top: 276px;
    font-size: 16px;
  }
  .back__email { font-weight: 600; font-style: italic; font-size: 21px; }
  .back__help {
    position: absolute; left: 0; right: 0; top: 305px;
    font-size: 17px; font-weight: 400;
  }
</style>
</head>
<body>
  <section class="card card--front">
    <svg class="front__water" viewBox="0 0 578 215" role="img" aria-label="Photo of a wave of splashing clear blue water">
      <defs>
        <linearGradient id="frontWater" x1="0" y1="0" x2="1" y2="0.35">
          <stop offset="0" stop-color="#5f9fd6"/>
          <stop offset="0.45" stop-color="#3d86c8"/>
          <stop offset="0.75" stop-color="#9cc9ec"/>
          <stop offset="1" stop-color="#4e95d0"/>
        </linearGradient>
        <linearGradient id="frontFade" x1="0" y1="0" x2="0" y2="1">
          <stop offset="0" stop-color="#ffffff" stop-opacity="0"/>
          <stop offset="1" stop-color="#ffffff" stop-opacity="1"/>
        </linearGradient>
      </defs>
      <rect width="578" height="215" fill="var(--water-pale)"/>
      <path d="M0 20 C120 20 260 30 380 80 C460 112 530 110 578 95 L578 170 C500 165 420 140 330 125 C220 110 100 120 0 105 Z" fill="url(#frontWater)"/>
      <rect width="578" height="215" fill="url(#frontFade)"/>
    </svg>
    <div class="brand">
      <span class="brand__dot"></span>
      <span class="brand__name">Cedar Hollow</span>
    </div>
    <div class="price-tag">PRICE $100</div>
  </section>

  <section class="card card--back">
    <svg class="back__water" viewBox="0 0 578 120" role="img" aria-label="Photo of rippling blue water surface">
      <defs>
        <linearGradient id="backWater" x1="0" y1="0" x2="0" y2="1">
          <stop offset="0" stop-color="#a9cfee"/>
          <stop offset="0.35" stop-color="#5c9bd4"/>
          <stop offset="1" stop-color="#0f6db8"/>
        </linearGradient>
        <linearGradient id="backBand" x1="0" y1="0" x2="1" y2="0">
          <stop offset="0" stop-color="#3f86c8"/>
          <stop offset="0.5" stop-color="#2a74ba"/>
          <stop offset="1" stop-color="#3c84c6"/>
        </linearGradient>
      </defs>
      <rect width="578" height="120" fill="url(#backWater)"/>
      <path d="M0 30 C150 10 300 5 420 20 C500 30 550 35 578 30 L578 70 C450 60 300 55 150 62 C90 65 40 60 0 55 Z" fill="url(#backBand)" opacity="0.6"/>
    </svg>
    <p class="back__usage">This card is to be used to<br>access water refills at any Cedar Hollow<br>water vending machines</p>
    <p class="back__contact-label">Please contact</p>
    <p class="back__phones">(869) 418 2930 <span class="back__or">or</span> (869) 534 1276</p>
    <p class="back__email-line">or&nbsp; <span class="back__email">clearflowbox@mailvista.example</span></p>
    <p class="back__help">for any assistance or recharging of card</p>
  </section>
</body>
</html>
```